Need Business Card for our Real Estate Business with Sales Executive's Picture

PANTONE 484 C ( RED)

PANTONE 2766 C ( BLUE

Industry/Entity Type

Real Estate

Contact Information for Business Card

Name, Mobile, email, & picture of Person
Agency Phone, address, Web address

Requirements
Must have
• Our Logo Colours, Agent Picture,

```html
<!DOCTYPE html>
<html lang="en">
<head>
<meta charset="utf-8">
<title>Dunmore Real Estate – Business Card</title>
<link rel="stylesheet" href="https://fonts.googleapis.com/css2?family=Work+Sans:wght@400;500;600&display=swap">
<style>
  :root {
    --navy: #1c2550;
    --red: #8f2a2a;
    --cream: #e6dccb;
    --gold: #dcc6a2;
    --card: #ebe7e1;
    --ink-soft: #6c6a68;
    --page: #d9d4cc;
  }
  * { margin: 0; padding: 0; box-sizing: border-box; }
  html, body { width: 1200px; height: 1047px; overflow: hidden; }
  body {
    background: var(--page);
    font-family: "Work Sans", Arial, sans-serif;
    position: relative;
  }
  .business-card {
    position: absolute;
    left: 80px; top: 240px;
    width: 1040px; height: 566px;
    border-radius: 22px;
    overflow: hidden;
    background: var(--card);
    box-shadow: 0 10px 30px rgba(0,0,0,0.12);
  }
  .card-artwork { position: absolute; inset: 0; }
  .brand-name {
    position: absolute;
    left: 60px; top: 92px;
    display: flex; align-items: center; gap: 18px;
    color: var(--navy);
    font-weight: 500;
  }
  .brand-mark { width: 22px; height: 22px; background: var(--red); flex: none; }
  .brand-words { line-height: 1; }
  .brand-words .primary { display: block; font-size: 66px; letter-spacing: 6px; }
  .brand-words .secondary { display: block; font-size: 20px; letter-spacing: 7px; margin-top: 12px; }
  .office-address {
    position: absolute;
    left: 60px; top: 318px;
    font-size: 22px; line-height: 31px;
    color: var(--ink-soft);
    font-style: normal;
  }
  .agent-details {
    position: absolute;
    right: 58px; top: 322px;
    text-align: right;
    color: var(--gold);
  }
  .agent-name { font-size: 38px; font-weight: 500; letter-spacing: 1px; line-height: 1.1; }
  .agent-role { font-size: 23px; letter-spacing: 0.6px; margin-top: 4px; }
  .contact-list { list-style: none; margin-top: 26px; font-size: 21px; letter-spacing: 0.5px; }
  .contact-list li {
    display: flex; justify-content: flex-end; align-items: center; gap: 16px;
    height: 29px;
  }
  .contact-list svg { width: 15px; height: 15px; flex: none; }
</style>
</head>
<body>
  <article class="business-card">
    <svg class="card-artwork" viewBox="0 0 1040 566" width="1040" height="566" aria-hidden="true">
      <path d="M0,362 C150,470 300,430 450,330 S640,195 720,182 L1040,158 V566 H0 Z" fill="var(--navy)"/>
      <path d="M0,428 C180,470 360,400 500,300 S660,196 730,186" fill="none" stroke="var(--cream)" stroke-width="14"/>
      <path d="M0,416 C180,456 360,388 500,288 S660,184 730,174" fill="none" stroke="var(--red)" stroke-width="9"/>
      <path d="M0,372 C120,420 220,420 320,400" fill="none" stroke="var(--cream)" stroke-width="6" opacity="0.8"/>
      <path d="M960,140 L1040,150 L1040,170 L960,160 Z" fill="var(--red)"/>
      <circle cx="851" cy="168" r="150" fill="var(--cream)"/>
      <circle cx="851" cy="168" r="142" fill="var(--navy)"/>
      <defs>
        <linearGradient id="portraitTone" x1="0" y1="0" x2="0" y2="1">
          <stop offset="0" stop-color="#eeece8"/>
          <stop offset="0.55" stop-color="#c9b8a8"/>
          <stop offset="1" stop-color="#2a3a6c"/>
        </linearGradient>
      </defs>
      <circle cx="851" cy="168" r="136" fill="url(#portraitTone)" role="img" aria-label="Portrait photo of the managing director in a navy suit"/>
    </svg>

    <div class="brand-name">
      <span class="brand-mark"></span>
      <span class="brand-words"><span class="primary">DUNMORE</span><span class="secondary">REAL ESTATE</span></span>
    </div>

    <address class="office-address">Via dei Tigli, 48.<br>12030 Revello (CN)</address>

    <section class="agent-details">
      <h1 class="agent-name">DANIEL HART</h1>
      <p class="agent-role">Managing Director</p>
      <ul class="contact-list">
        <li>+852 2481 0617
          <svg viewBox="0 0 16 16"><path d="M4 1.5l2.5 3-1.5 1.5c.8 2 2.5 3.7 4.5 4.5L11 9l3 2.5-1.5 2.5C7 14 2 9 2 3z" fill="var(--gold)"/></svg>
        </li>
        <li>+852 2481 0692
          <svg viewBox="0 0 16 16"><rect x="4" y="2" width="8" height="4" fill="var(--gold)"/><rect x="2" y="6" width="12" height="6" rx="1" fill="var(--gold)"/><rect x="4" y="10" width="8" height="4" fill="var(--gold)"/></svg>
        </li>
        <li>info@dunmorerealestate.com
          <svg viewBox="0 0 16 16"><rect x="2" y="3.5" width="12" height="9" fill="none" stroke="var(--gold)" stroke-width="1.5"/><path d="M2 4l6 5 6-5" fill="none" stroke="var(--gold)" stroke-width="1.5"/></svg>
        </li>
        <li>www.dunmorerealestate.com
          <svg viewBox="0 0 16 16"><circle cx="8" cy="8" r="6" fill="none" stroke="var(--gold)" stroke-width="1.4"/><ellipse cx="8" cy="8" rx="2.6" ry="6" fill="none" stroke="var(--gold)" stroke-width="1.2"/><path d="M2 8h12" stroke="var(--gold)" stroke-width="1.2"/></svg>
        </li>
      </ul>
    </section>
  </article>
</body>
</html>
```